Defense contractor needs a roll-up for an exhibition

The booth we have booked has only a size of 3m².
So this will be the centerpiece of the whole booth.
We need a roll-up that attracts visitors and at the same time it should contain already designed graphics. These graphics are giving visitors an overview of our system. So it is necessary to have them exposed in a height that the booth personal can conveniently point with its fingers at them.
For information about our company and product visit:
https://www.brellowtrackline.com/
For designing you should use Adobe Illustrator and the templates provided in the zip file, to guarantee a perfect print.
I have supplied my business card that you can copy the logo. As the company logo will be already at the booth nearby the top of the roll-up, you should not place it there. It can be in the middle or at the bottom.
I have uploaded a picture of the booth. The roll up will be placed at the left of the screen and has a size of 80cm x 200cm

Defense

Defense

Serif

0054AA
0677BA
7BADD7
CADEEF
E8F1F8

• you must use the Adobe Illustrator template to have a good printing result
• company logo on the upper side of the roll-up

```html
<!DOCTYPE html>
<html lang="en">
<head>
<meta charset="utf-8">
<title>Brellow Trackline Roll-up</title>
<link href="https://fonts.googleapis.com/css2?family=Bebas+Neue&family=Open+Sans:wght@400;600;700&display=swap" rel="stylesheet">
<style>
  :root {
    --navy: #1f3f9c;
    --blue: #2a4fb0;
    --deep: #14307f;
    --ink: #2b3a8f;
    --lavender: #e3e5f2;
    --white: #ffffff;
    --black: #141418;
    --stage: #d6d7da;
    --rule: #b9bdd3;
    --scene-light: #eceef8;
    --scene-mid: #c9cde4;
    --scene-shade: #9fa8d6;
    --scene-grey: #bfc0c8;
    --frame: #8e97c7;
  }
  * { margin: 0; padding: 0; box-sizing: border-box; }
  html, body { width: 1200px; height: 900px; overflow: hidden; background: var(--stage); }
  .rollup {
    position: absolute; left: 420px; top: 10px; width: 360px; height: 880px;
    background: var(--lavender); overflow: hidden;
    font-family: "Open Sans", Arial, sans-serif;
    box-shadow: 0 4px 14px rgba(0,0,0,.25);
  }
  .header { position: absolute; left: 0; top: 0; width: 360px; height: 100px; background: var(--white); }
  .header h1 {
    position: absolute; top: 26px; width: 100%; text-align: center;
    font-family: "Bebas Neue", "Oswald", sans-serif; font-weight: 400;
    font-size: 27px; line-height: 27px; color: var(--black); letter-spacing: .2px;
  }
  .header-slash { position: absolute; left: 0; top: 90px; }
  .visual { position: absolute; left: 0; width: 360px; }
  .visual::after {
    content: ""; position: absolute; inset: 10px 14px;
    border: 1px dashed var(--frame); border-radius: 3px;
  }
  .visual-field {
    top: 100px; height: 202px;
    background:
      radial-gradient(ellipse 90px 60px at 70% 68%, var(--scene-grey), transparent 75%),
      radial-gradient(ellipse 80px 45px at 24% 42%, var(--scene-mid), transparent 75%),
      radial-gradient(ellipse 110px 30px at 62% 22%, var(--scene-mid), transparent 75%),
      radial-gradient(ellipse 140px 40px at 68% 88%, var(--scene-shade), transparent 75%),
      linear-gradient(160deg, var(--scene-light), #dcdff0);
  }
  .visual-room {
    top: 427px; height: 190px;
    background:
      radial-gradient(ellipse 90px 55px at 66% 30%, var(--scene-grey), transparent 75%),
      radial-gradient(ellipse 120px 50px at 44% 68%, var(--scene-mid), transparent 75%),
      radial-gradient(ellipse 60px 40px at 18% 30%, var(--scene-mid), transparent 75%),
      radial-gradient(ellipse 150px 30px at 55% 90%, var(--scene-shade), transparent 75%),
      linear-gradient(160deg, var(--scene-light), #d8dbee);
  }
  .intro {
    position: absolute; left: 0; top: 302px; width: 360px; height: 125px;
    background: linear-gradient(90deg, var(--deep), var(--blue));
    color: var(--white);
  }
  .brand-name {
    position: absolute; top: 24px; width: 100%; text-align: center;
    font-weight: 700; font-size: 16px; letter-spacing: .5px; text-transform: uppercase;
  }
  .intro p {
    position: absolute; left: 16px; right: 16px; top: 62px;
    font-size: 7.9px; line-height: 10.8px; color: #e6eaf7; text-align: justify;
  }
  .features { position: absolute; left: 0; top: 620px; width: 360px; height: 128px; }
  .feature {
    position: absolute; width: 80px; text-align: center;
    color: var(--ink); font-size: 6.8px; font-weight: 700; line-height: 8.4px; text-transform: uppercase;
  }
  .feature svg { display: block; margin: 0 auto 4px; }
  .grid-line { position: absolute; background: var(--rule); }
  .footer-shape { position: absolute; left: 0; top: 720px; }
  .contact { position: absolute; left: 25px; top: 768px; color: var(--white); }
  .contact h2 {
    font-family: "Bebas Neue", "Oswald", sans-serif; font-weight: 400; font-size: 19px; letter-spacing: .3px;
  }
  .contact-line { display: flex; align-items: center; gap: 6px; font-size: 9.5px; font-weight: 600; margin-top: 5px; }
</style>
</head>
<body>
<div class="rollup">
  <header class="header">
    <h1>Advanced Combat Training Systems<br>For Realistic Combat Simulation</h1>
    <svg class="header-slash" width="360" height="10" viewBox="0 0 360 10">
      <polygon points="150,4 360,4 360,10 144,10" fill="var(--navy)"/>
    </svg>
  </header>

  <div class="visual visual-field" role="img" aria-label="Isometric illustration of two tanks, three target stands and a mobile instructor truck with screens and soldiers"></div>

  <section class="intro">
    <div class="brand-name">Brellow Trackline</div>
    <p>KESTRA (Kinetic Evaluation System for Tracking, Range And Analysis) allows for a modern approach to duel simulation, firing range training, armored vehicle driving training, and simulation debriefing through an integrated system of sensors, optics, and controls that give soldiers and instructors real-time, real-world vision and data.</p>
  </section>

  <div class="visual visual-room" role="img" aria-label="Isometric illustration of a debriefing room with instructors at desks facing two large wall screens"></div>

  <section class="features">
    <div class="grid-line" style="left:99px;top:2px;width:1px;height:120px"></div>
    <div class="grid-line" style="left:179px;top:2px;width:1px;height:120px"></div>
    <div class="grid-line" style="left:261px;top:2px;width:1px;height:120px"></div>
    <div class="grid-line" style="left:19px;top:66px;width:321px;height:1px"></div>

    <div class="feature" style="left:15px;top:4px">
      <svg width="22" height="34" viewBox="0 0 22 34" fill="none" stroke="var(--ink)" stroke-width="1.6"><rect x="6" y="9" width="10" height="23" rx="2"/><circle cx="11" cy="15" r="2"/><path d="M9 21h4M9 25h4M9 28h4"/><path d="M7 5a6 6 0 0 1 8 0M9 7a3 3 0 0 1 4 0"/></svg>
      Remote-control<br>functions
    </div>
    <div class="feature" style="left:100px;top:4px">
      <svg width="34" height="34" viewBox="0 0 34 34" fill="none" stroke="var(--ink)" stroke-width="1.6"><rect x="3" y="6" width="28" height="5"/><path d="M6 11a11 11 0 0 0 22 0"/><circle cx="17" cy="17" r="4"/><path d="M12 28a7 7 0 0 0 10 0"/></svg>
      16 camera systems<br>per vehicle
    </div>
    <div class="feature" style="left:180px;top:4px">
      <svg width="34" height="34" viewBox="0 0 34 34" fill="none" stroke="var(--ink)" stroke-width="1.6"><path d="M4 12h7l3-4h6l3 4h7v17H4z"/><circle cx="17" cy="20" r="6"/><circle cx="17" cy="20" r="3"/></svg>
      Optics<br>camera
    </div>
    <div class="feature" style="left:261px;top:4px">
      <svg width="26" height="34" viewBox="0 0 26 34" fill="none" stroke="var(--ink)" stroke-width="1.6"><rect x="4" y="3" width="18" height="28" rx="2"/><path d="M7 8h12M7 12h9M7 16h12M7 20h9M7 24h12"/></svg>
      Vehicle<br>data
    </div>

    <div class="feature" style="left:15px;top:72px">
      <svg width="26" height="30" viewBox="0 0 26 30" fill="none" stroke="var(--ink)" stroke-width="2.2"><circle cx="11" cy="12" r="7"/><path d="M16 17l7 8"/></svg>
      Full instructor<br>overview
    </div>
    <div class="feature" style="left:100px;top:72px">
      <svg width="26" height="30" viewBox="0 0 26 30" fill="none" stroke="var(--ink)" stroke-width="1.6"><path d="M16 4v16a4 4 0 1 1-4 0V4a2 2 0 0 1 4 0z"/><path d="M10 10a6 6 0 0 0 0 10"/><circle cx="14" cy="23" r="2" fill="var(--ink)"/></svg>
      Air-conditioned<br>instructor
    </div>
    <div class="feature" style="left:180px;top:72px">
      <svg width="30" height="30" viewBox="0 0 30 30" fill="none" stroke="var(--ink)" stroke-width="1.6"><path d="M5 18v-4a10 10 0 0 1 20 0v4"/><rect x="3" y="16" width="4" height="7" rx="1"/><rect x="23" y="16" width="4" height="7" rx="1"/><path d="M11 15v4M14 12v10M17 14v6M20 16v2"/></svg>
      Full data<br>recording
    </div>
    <div class="feature" style="left:261px;top:72px">
      <svg width="34" height="30" viewBox="0 0 34 30" fill="none" stroke="var(--ink)" stroke-width="1.6"><path d="M3 26L14 6l5 8 3-4 9 16z"/><path d="M17 17v6M14 20h6M15 18l4 4M19 18l-4 4"/></svg>
      All-weather &amp;<br>all-terrain
    </div>
  </section>

  <svg class="footer-shape" width="360" height="160" viewBox="0 720 360 160">
    <defs>
      <linearGradient id="footerBlue" x1="0" y1="0" x2="1" y2="1">
        <stop offset="0" stop-color="#1d3c9a"/>
        <stop offset="1" stop-color="#2f57bd"/>
      </linearGradient>
    </defs>
    <polygon points="0,740 244,796 360,824 360,880 0,880" fill="url(#footerBlue)"/>
    <polygon points="244,796 360,759 360,824" fill="var(--black)"/>
  </svg>

  <div class="contact">
    <h2>Contact Us</h2>
    <div class="contact-line">
      <svg width="11" height="11" viewBox="0 0 11 11"><rect width="11" height="11" rx="2" fill="var(--white)"/><path d="M3 2.5l1.5 0 .6 1.8-.9.7a5 5 0 0 0 2 2l.7-.9 1.8.6v1.5a1 1 0 0 1-1 .8A6 6 0 0 1 2.2 3.5a1 1 0 0 1 .8-1z" fill="var(--navy)"/></svg>
      +49 170 555 0192
    </div>
    <div class="contact-line">
      <svg width="11" height="11" viewBox="0 0 11 11"><rect width="11" height="11" rx="2" fill="var(--white)"/><circle cx="5.5" cy="5.5" r="3.3" fill="none" stroke="var(--navy)" stroke-width=".9"/><path d="M2.2 5.5h6.6M5.5 2.2c-1.5 2-1.5 4.6 0 6.6M5.5 2.2c1.5 2 1.5 4.6 0 6.6" fill="none" stroke="var(--navy)" stroke-width=".7"/></svg>
      www.brellowtrackline.com
    </div>
  </div>
</div>
</body>
</html>
```